'Held Forever' Need help with logo. It is an Acrylic Baby hand and foot / pet paw / clay impress

The printing parameters are 3 colors (any) and 2 fonts (any) onto a white box.
*This product is for private label selling on Vendora.
*We need a logo for 'Held Forever' to go on our packaging. A package template has been provided.
*It comes in a kit, we would like a, 'Whats inside the box section'.
1 Acrylic Frame.
2 Stainless Steel Stands.
2 Stainless Steel Screws.
1 40 gram Packet of Air Dry Clay.
1 Mini Roller.
1 Letter and Number Stencil.
*Mention that the clay is White completely safe for baby, non-toxic etc. I have provided the certification for the clay in the upload (EN71, D2016.PDF)
*The Bar code is an FNSKU which is to be printed clearly on the outside of the box. I have uploaded the file. All you need is the bar code and the alphanumeric code. The Text underneath is not to be used.
*Instructions for clay to be printed on the back of the box. I have uploaded a file which contains photos. The photos are only their to provide designers with a visual and are not to be used on the packaging. However I would like some basic small sketches drawn up so the customer can follow along visually to what is written in the text. Be as creative as you want and see it from the customers point of view. i.e. Are these easy to follow instructions? Clear? etc.
*I Have also provided a Product Description upload which shows the assembled product complete with clay imprint for the designer to visualize what we are selling. It also includes aspects of the product that the competitors DO NOT have so if the designer could somehow weave this into the packaging design that would be perfect.
*I have also uploaded pictures of the frame (without clay or photos) and clay,roller and stencil to help the designer visually.

Target Market(s)

Baby Keepsake
Pet Keepsake
Any memorable moment that can be Held Forever

Industry/Entity Type

Baby

Colors

Designer to choose colors to be used in the design.

Requirements
Must have
• FNSKU/bar code printed on the outside of box
• Instructions on the back of box. All the text provided must be used. with basic drawings.
• A logo that 'POPS'
• What's inside the box.
• Made in China
• Non-toxic 100% baby safe clay
Nice to have
• Any good ideas I can't think of!

```html
<!DOCTYPE html>
<html lang="en">
<head>
<meta charset="utf-8">
<title>Held Forever – Packaging Front</title>
<link rel="stylesheet" href="https://fonts.googleapis.com/css2?family=Open+Sans:wght@300;700&display=swap">
<style>
  :root {
    --bg: #d9d9d9;
    --box: #030303;
    --pattern-light: #4a4a4a;
    --pattern-mid: #262626;
    --pattern-dark: #070707;
    --ink: #ffffff;
    --silver: #d9d9d9;
    --icon-fill: #2a2a2a;
  }
  * { margin: 0; padding: 0; box-sizing: border-box; }
  html, body {
    width: 1200px;
    height: 1006px;
    overflow: hidden;
    background: var(--bg);
    font-family: "Open Sans", Arial, sans-serif;
  }
  .box-front {
    position: absolute;
    left: 150px;
    top: 130px;
    width: 900px;
    height: 740px;
    background: var(--box);
  }
  .pattern-band {
    position: absolute;
    left: 0;
    top: 90px;
    width: 100%;
    height: 450px;
    background:
      radial-gradient(ellipse 30% 40% at 20% 45%, rgba(90,90,90,0.55), transparent 70%),
      radial-gradient(ellipse 30% 40% at 80% 45%, rgba(90,90,90,0.55), transparent 70%),
      radial-gradient(ellipse 45% 45% at 50% 45%, var(--pattern-light), var(--pattern-mid) 55%, transparent 100%),
      linear-gradient(180deg, var(--pattern-dark) 0%, #1a1a1a 45%, var(--pattern-dark) 100%);
    -webkit-mask-image: linear-gradient(180deg, transparent 0%, #000 20%, #000 75%, transparent 100%);
            mask-image: linear-gradient(180deg, transparent 0%, #000 20%, #000 75%, transparent 100%);
  }
  .brand-seal {
    position: absolute;
    left: 325px;
    top: 200px;
    width: 250px;
    height: 250px;
    border-radius: 50%;
    border: 6px solid var(--silver);
    background: var(--box);
    display: flex;
    align-items: center;
    justify-content: center;
  }
  .brand-name {
    text-align: center;
    font-weight: 300;
    font-size: 50px;
    line-height: 54px;
    letter-spacing: 2px;
    text-transform: uppercase;
    color: var(--silver);
  }
  .feature {
    position: absolute;
    text-align: center;
    color: var(--ink);
    font-weight: 700;
    font-size: 10.5px;
    line-height: 13px;
    white-space: nowrap;
  }
  .feature svg { display: block; margin: 0 auto 6px; }
  .feature-kit { left: 30px; top: 530px; width: 240px; }
  .feature-safe { left: 280px; top: 580px; width: 100px; }
  .feature-modern { left: 440px; top: 610px; width: 120px; }
  .feature-strong { left: 630px; top: 645px; width: 120px; }
  .kit-icons { display: flex; justify-content: center; align-items: center; gap: 4px; margin-bottom: 6px; }
  .icon-spot {
    width: 40px; height: 40px; border-radius: 50%;
    background: var(--icon-fill);
    border: 2px solid var(--ink);
  }
  .icon-divider { color: var(--ink); font-size: 30px; font-weight: 300; line-height: 40px; }
</style>
</head>
<body>
  <main class="box-front">
    <div class="pattern-band" role="img" aria-label="Repeating grey triangle pattern that fades into the black box"></div>

    <div class="brand-seal">
      <h1 class="brand-name">Held<br>Forever</h1>
    </div>

    <div class="feature feature-kit">
      <div class="kit-icons">
        <div class="icon-spot" role="img" aria-label="Baby icon"></div>
        <span class="icon-divider">/</span>
        <div class="icon-spot" role="img" aria-label="Puppy icon"></div>
      </div>
      Baby hand and footprint picture frame kit.<br>For pet lovers paw prints ect.
    </div>

    <div class="feature feature-safe">
      <svg width="42" height="42" viewBox="0 0 40 40" aria-hidden="true">
        <circle cx="20" cy="20" r="17" fill="none" stroke="#fff" stroke-width="2"/>
        <path d="M16 9h8M17 9v9l-6 11h18l-6-11V9" fill="none" stroke="#fff" stroke-width="2" stroke-linejoin="round"/>
        <line x1="8" y1="8" x2="32" y2="32" stroke="#fff" stroke-width="2"/>
      </svg>
      Non toxic
    </div>

    <div class="feature feature-modern">
      <svg width="30" height="42" viewBox="0 0 30 40" aria-hidden="true">
        <path d="M15 2a11 11 0 0 0-7 19.5c1.5 1.3 2 3 2 5V29h10v-2.5c0-2 .5-3.7 2-5A11 11 0 0 0 15 2z" fill="none" stroke="#fff" stroke-width="2"/>
        <path d="M11 32h8M12 35h6M12 16l3 4 3-4" fill="none" stroke="#fff" stroke-width="2"/>
      </svg>
      Look modern
    </div>

    <div class="feature feature-strong">
      <svg width="58" height="42" viewBox="0 0 58 42" aria-hidden="true">
        <path d="M12 2h34l10 12-27 26L2 14z" fill="#bdbdbd" stroke="#fff" stroke-width="2" stroke-linejoin="round"/>
        <path d="M2 14h54M20 2l-6 12 15 26 15-26-6-12M29 2l-9 12M29 2l9 12" fill="none" stroke="#fff" stroke-width="1.5"/>
      </svg>
      High resistance
    </div>
  </main>
</body>
</html>
```